Exclusive beauty salon needs a price list or services booklet

I need a new very attractive flyer for my beauty salon, containing information on the different services and their prices.
In attachment you can find a pdf of the "old" one, but I'd love to have a beautifully designed new one!
I'd love to have a booklet in format 148 x 148 mm, or in US format, containing 12 or 16 pages, but if you can offer other nice looking designs they are welcome!
The services that need to come in the booklet with their prices can all be found on my website: www.atelierverano.be, starting with
Gelaatsverzorging
Wimperverlenging
Suikerontharing
Wimperlifting
Permanente Make Up
Airbrush Tanning

Target Market(s)

woman from 20 to 89 years old

Industry/Entity Type

Beauty Salon

Font styles to use
Sans Serif

Colors

Designer to choose colors to be used in the design.

Requirements
Must have
• a classy nice look, it must contain details about the services from my beauty salon and their prices, and nice pictures.
• The Names, prices and explanations of the services can easily be found on my website: www.atelierverano.be
Nice to have
• In attachment you can find the "old" price list in pdf, what I need now is a "new booklet" with the new logo and updated services price list.
• I need a very nice and attractive looking booklet, classy chique, Paris chique, looking very expensive.
Should not have
• Not too much colors, not too curly, but still feminine

```html
<!DOCTYPE html>
<html lang="nl">
<head>
<meta charset="utf-8">
<title>Permanente Make-Up – Tarieven</title>
<link href="https://fonts.googleapis.com/css2?family=Source+Sans+3:ital,wght@0,400;0,600;1,400&display=swap" rel="stylesheet">
<style>
  :root {
    --frame: #a7a8ab;
    --paper: #ffffff;
    --teal: #6ec6d1;
    --text: #8c8c8c;
    --label: #8f8f8f;
    --skin-light: #f3ddd0;
    --skin-mid: #e2b7a0;
    --skin-deep: #c9927a;
  }
  * { margin: 0; padding: 0; box-sizing: border-box; }
  html, body { width: 1200px; height: 866px; overflow: hidden; }
  body {
    background: var(--frame);
    font-family: "Source Sans 3", "Myriad Pro", Arial, sans-serif;
    position: relative;
  }
  .page {
    position: absolute;
    left: 34px; top: 34px;
    width: 586px; height: 798px;
    background: var(--paper);
  }
  .photo {
    position: absolute;
    left: 620px; top: 34px;
    width: 546px; height: 798px;
    background:
      radial-gradient(ellipse at 65% 60%, var(--skin-light) 0%, var(--skin-mid) 55%, var(--skin-deep) 100%);
  }
  .intro-title {
    position: absolute;
    left: 42px; top: 45px;
    font-size: 26px;
    font-weight: 400;
    color: var(--teal);
    letter-spacing: 0.1px;
  }
  .reasons {
    position: absolute;
    left: 42px; top: 90px;
    width: 500px;
    list-style: none;
  }
  .reasons li {
    position: relative;
    padding-left: 22px;
    font-size: 17.5px;
    font-style: italic;
    line-height: 24px;
    color: var(--text);
    margin-bottom: 4px;
  }
  .reasons svg {
    position: absolute;
    left: 2px; top: 8px;
    width: 11px; height: 9px;
  }
  .rates-title {
    position: absolute;
    left: 42px; top: 378px;
    font-size: 25px;
    font-weight: 400;
    color: var(--teal);
  }
  .rates {
    position: absolute;
    left: 42px; top: 422px;
    width: 534px;
    list-style: none;
  }
  .rates li {
    display: flex;
    justify-content: space-between;
    align-items: flex-start;
    font-style: italic;
    font-size: 22px;
    line-height: 26px;
    margin-bottom: 12px;
  }
  .rates .service { color: var(--label); width: 410px; }
  .rates .price { color: var(--teal); }
</style>
</head>
<body>
  <section class="page">
    <h2 class="intro-title">Wanneer is Permanente Make-Up Zinvol?</h2>
    <ul class="reasons">
      <li><svg viewBox="0 0 11 9"><path d="M1 4.5 L4 7.5 L10 1" fill="none" stroke="#6ec6d1" stroke-width="2"/></svg>U wil er beter uitzien waardoor u zich beter voelt</li>
      <li><svg viewBox="0 0 11 9"><path d="M1 4.5 L4 7.5 L10 1" fill="none" stroke="#6ec6d1" stroke-width="2"/></svg>U wil een natuurlijke uitstraling, elke dag opnieuw</li>
      <li><svg viewBox="0 0 11 9"><path d="M1 4.5 L4 7.5 L10 1" fill="none" stroke="#6ec6d1" stroke-width="2"/></svg>U zoekt een waterbestendige make- up, geen make- up die uitloopt wanneer u geniet van wellness.</li>
      <li><svg viewBox="0 0 11 9"><path d="M1 4.5 L4 7.5 L10 1" fill="none" stroke="#6ec6d1" stroke-width="2"/></svg>Omwille van motorische of gezichtsproblemen is het moeilijk u correct te maquilleren</li>
      <li><svg viewBox="0 0 11 9"><path d="M1 4.5 L4 7.5 L10 1" fill="none" stroke="#6ec6d1" stroke-width="2"/></svg>U beheerst niet de tekenkunst om u juist te maquilleren</li>
      <li><svg viewBox="0 0 11 9"><path d="M1 4.5 L4 7.5 L10 1" fill="none" stroke="#6ec6d1" stroke-width="2"/></svg>Beroepshalve bent u genoodzaakt er steeds gemaquilleerd, verzorgd uit te zien</li>
    </ul>

    <h2 class="rates-title">TARIEVEN</h2>
    <ul class="rates">
      <li><span class="service">Full lips</span><span class="price">€595</span></li>
      <li><span class="service">Permanente make up volledige oogcontou</span><span class="price">€360</span></li>
      <li><span class="service">Brede eyeliner boven het oog</span><span class="price">€235</span></li>
      <li><span class="service">Fijne eyeliner boven (wimperinvulling) het oog</span><span class="price">€186</span></li>
      <li><span class="service">Wenkbrauwen hairstroke techniek</span><span class="price">€320</span></li>
      <li><span class="service">Wenkbrauwen shading brow of poederwenkbrauw</span><span class="price">€320</span></li>
      <li><span class="service">Wenkbrauwen power brow</span><span class="price">€320</span></li>
    </ul>
  </section>

  <div class="photo" role="img" aria-label="Foto: permanente make-up van de wenkbrauwen wordt aangebracht met een pigmenteerpen"></div>
</body>
</html>
```